"Harbor Builders" is a residential building company and needs a new business card design and may re

We would like a redesign based on the existing logo, and would like to see a new font as well. We are bespoke home builders who build sustainable energy efficient homes.

Industry/Entity Type

Construction

Contact Information for Business Card

Business card size 40mm x 90mm

Colors

Designer to choose colors to be used in the design.

```html
<!DOCTYPE html>
<html lang="en">
<head>
<meta charset="utf-8">
<title>Harbor Builders – Business Card</title>
<link rel="stylesheet" href="https://fonts.googleapis.com/css2?family=Roboto:wght@400;500&family=Roboto+Condensed:wght@700&family=Open+Sans:wght@600&display=swap">
<style>
  :root {
    --backdrop: #2b2b2b;
    --card-white: #f3f3f3;
    --lime: #bdd631;
    --ink: #111111;
    --text-grey: #4a4a4a;
    --rule: #6b7a2a;
    --pattern-grey: #e2e2e2;
  }
  * { margin: 0; padding: 0; box-sizing: border-box; }
  html, body { width: 1200px; height: 960px; overflow: hidden; }
  body {
    background: var(--backdrop);
    position: relative;
    font-family: "Roboto", Arial, sans-serif;
  }
  .card {
    position: absolute;
    width: 600px;
    height: 343px;
    background: var(--card-white);
    overflow: hidden;
  }
  .card--front { left: 302px; top: 129px; }
  .card--back { left: 299px; top: 488px; }

  .front__band { position: absolute; inset: 0; }

  .brand {
    position: absolute;
    display: flex;
    align-items: center;
    gap: 12px;
    font-family: "Open Sans", Arial, sans-serif;
    font-weight: 600;
    color: var(--ink);
  }
  .brand__square { background: var(--lime); }
  .card--front .brand { left: 0; right: 0; top: 54px; justify-content: center; font-size: 30px; }
  .card--front .brand__square { width: 22px; height: 22px; }

  .holder {
    position: absolute;
    left: 28px; right: 30px; top: 180px;
    font-family: "Roboto Condensed", Arial, sans-serif;
    font-weight: 700;
    font-size: 23px;
    color: var(--ink);
    padding-bottom: 6px;
    border-bottom: 1px solid var(--rule);
  }
  .details {
    position: absolute;
    left: 30px; top: 222px;
    font-size: 15px;
    line-height: 18px;
    color: var(--text-grey);
    list-style: none;
  }
  .details__contact { margin-top: 5px; }
  .details__contact li { display: flex; align-items: center; gap: 8px; }
  .details__contact svg { width: 13px; height: 13px; fill: var(--ink); }
  .address {
    position: absolute;
    right: 31px; top: 251px;
    text-align: right;
    font-style: normal;
    font-size: 15px;
    line-height: 18px;
    color: var(--text-grey);
  }
  .address strong { font-weight: 500; }

  .back__pattern {
    position: absolute; inset: 0;
    background: linear-gradient(180deg, var(--pattern-grey), #ececec 50%, var(--pattern-grey));
  }
  .card--back .brand { left: 0; right: 0; top: 140px; justify-content: center; font-size: 40px; }
  .card--back .brand__square { width: 30px; height: 30px; }
  .back__web {
    position: absolute;
    left: 0; right: 0; top: 298px;
    text-align: center;
    font-size: 15px;
    letter-spacing: 3px;
    color: var(--text-grey);
  }
</style>
</head>
<body>
  <section class="card card--front">
    <svg class="front__band" width="600" height="343" viewBox="0 0 600 343">
      <polygon points="0,91 302,166 600,89 600,343 0,343" fill="var(--lime)"/>
      <polyline points="0,91 302,166 600,89" fill="none" stroke="var(--ink)" stroke-width="5"/>
    </svg>
    <div class="brand"><span class="brand__square"></span>Harbor Builders</div>
    <h1 class="holder">DANIEL WHITMORE</h1>
    <div class="details">
      <div>Registration 40718</div>
      <div>ABN: 52 309 614 207</div>
      <ul class="details__contact">
        <li><svg viewBox="0 0 12 12"><path d="M3 0h6a1 1 0 0 1 1 1v10a1 1 0 0 1-1 1H3a1 1 0 0 1-1-1V1a1 1 0 0 1 1-1zm0 2v7h6V2z"/></svg>0400 555 018</li>
        <li><svg viewBox="0 0 12 12"><path d="M1 3h10v7H1zM1 3l5 4 5-4" stroke="var(--lime)" stroke-width="0.8"/></svg>daniel@harborbuilders.example</li>
        <li><svg viewBox="0 0 12 12"><circle cx="6" cy="6" r="5.5"/><path d="M3 4q2 0 2 2t2 3M8 2q-1 2 1 3" stroke="var(--lime)" stroke-width="1" fill="none"/></svg>www.harborbuilders.example</li>
      </ul>
    </div>
    <address class="address">
      <strong>Harbor Builders Pty Ltd</strong><br>
      PO Box 7720<br>
      Eastgate<br>
      LPO Northbay WA 6099
    </address>
  </section>

  <section class="card card--back">
    <div class="back__pattern" role="img" aria-label="Faint repeating brand pattern across the card back"></div>
    <div class="brand"><span class="brand__square"></span>Harbor Builders</div>
    <p class="back__web">www.harborbuilders.example</p>
  </section>
</body>
</html>
```